The logo name is "Harbor Skin". The name of the product will be "Cutaneous Comfort". This product is specifically formulated for amputees. Therefore under the product name it should state "for amputees". The catch phrase will be "Experience Harbor find Calmness"
These are the things we need on the label:
Logo, product name, "for amputees", "Experience Harbor find Calmness", Safe, Effective, Directions: spray on problem areas, no need to dry off. harborskin.example, Made in Canada, 500ml.
The MOST IMPORTANT and therefore the most prominent thing on this lable will be the LOGO! The second most prominent thing will be the word "Comfort" We want to keep it very plain, very simple, very unclutered. Keep in mind that this lable will be placed on a white bottle or have a white back ground. The 500ml white PE bottle with trigger sprayer will have a tear drop label. See attached die line (S-294).
We want to stay with the colours that goes with the colour scheme of the logo. See attached logo. Soft colours. We do not want a picture! We would like the lable to be classy and rich.
Updates
The logo name is "Harbor Skin". The name of the product will be "Cutaneous Comfort". This product is specificlly formulated for amputees. Therefore under the product name it should state "for amputees". The catch phrase will be "Experience Harbor find Calmness"
Logo, product name, "for amputees", catch phrase "Experience Harbor find Calmness", Clean, Safe, Effective, Directions: spray on problem areas, no need to dry off. Also Harbor Skin Corpation, harborskin.example, Made in Canada, 500ml.
We want to stay with the colour scheme of the logo. See attached logo. Soft colours. We do not want a picture! We would like the lable to be classy and rich.
This is the offical directive that came from the governing panal of this lable. This panal it not know where it wanted to take this lable that would represent this line until they review all of your submissions, thank you for all your talented hard work. But now it is clear it is time to regroup and hit this objective.
Project Deadline Extended
Reason: New restrictions on lable wording for this product.
Target Market(s)
Amputees and Parents of.
Industry/Entity Type
Product
Requirements
Must have
- Final product to be in a pdf or an illustrator file

```html
<!DOCTYPE html>
<html lang="en">
<head>
<meta charset="utf-8">
<title>Harbor Skin – Cutaneous Comfort Label</title>
<link href="https://fonts.googleapis.com/css2?family=Montserrat:ital,wght@0,600;0,700;0,800;1,800&family=Roboto+Condensed:wght@700&display=swap" rel="stylesheet">
<style>
  :root {
    --green-deep: #0d4536;
    --green-mid: #1a7a64;
    --green-soft: #23907a;
    --teal-accent: #4fb596;
    --orange: #f7a023;
    --ink: #0f3d2e;
    --white: #ffffff;
    --outline: #b9b9b9;
    --caption: #111111;
  }
  html, body {
    margin: 0;
    width: 1200px;
    height: 900px;
    overflow: hidden;
    background: var(--white);
  }
  .canvas {
    position: relative;
    width: 1200px;
    height: 900px;
  }
  .label-art {
    position: absolute;
    inset: 0;
  }
  .brand-name { font-family: "Montserrat", sans-serif; font-weight: 700; fill: var(--ink); }
  .claim { font-family: "Montserrat", sans-serif; font-weight: 700; fill: var(--white); }
  .product-line { font-family: "Montserrat", sans-serif; font-weight: 800; fill: var(--green-mid); }
  .product-key { font-family: "Montserrat", sans-serif; font-weight: 800; fill: var(--ink); }
  .audience { font-family: "Montserrat", sans-serif; font-weight: 800; font-style: italic; fill: var(--white); }
  .tagline { font-family: "Roboto Condensed", sans-serif; font-weight: 700; fill: var(--ink); }
  .fine-print { font-family: "Roboto Condensed", sans-serif; font-weight: 700; fill: var(--white); }
  .volume { font-family: "Roboto Condensed", sans-serif; font-weight: 700; fill: var(--white); }
  .panel-caption {
    position: absolute;
    left: 0;
    width: 1208px;
    top: 776px;
    text-align: center;
    font-family: "Montserrat", sans-serif;
    font-weight: 700;
    font-size: 15px;
    color: var(--caption);
    margin: 0;
  }
</style>
</head>
<body>
<main class="canvas">
  <svg class="label-art" width="1200" height="900" viewBox="0 0 1200 900" aria-label="Teardrop label, front panel">
    <defs>
      <clipPath id="teardrop-clip">
        <path id="teardrop" d="M683,103 C722,135 772,265 785,420 L785,722 Q785,752 758,752 L442,752 Q415,752 415,722 L415,600 C418,420 520,205 683,103 Z"/>
      </clipPath>
      <radialGradient id="green-top" cx="0.55" cy="0.2" r="0.8">
        <stop offset="0" stop-color="var(--green-soft)"/>
        <stop offset="1" stop-color="var(--green-deep)"/>
      </radialGradient>
      <radialGradient id="green-bottom" cx="0.45" cy="0.75" r="0.7">
        <stop offset="0" stop-color="var(--green-soft)"/>
        <stop offset="1" stop-color="var(--green-deep)"/>
      </radialGradient>
    </defs>

    <g class="label-body" clip-path="url(#teardrop-clip)">
      <rect x="400" y="90" width="400" height="680" fill="var(--white)"/>

      <!-- top swoosh -->
      <path class="swoosh-orange-top" d="M400,90 L800,90 L800,222 C660,226 540,270 478,362 L400,362 Z" fill="var(--orange)"/>
      <path class="swoosh-green-top" d="M400,90 L800,90 L800,212 C655,218 530,262 470,350 L400,350 Z" fill="url(#green-top)"/>

      <!-- bottom wave -->
      <path class="wave-orange" d="M400,495 L415,495 C455,600 610,650 800,585 L800,770 L400,770 Z" fill="var(--orange)"/>
      <path class="wave-green" d="M400,540 L415,540 C468,680 650,700 800,636 L800,770 L400,770 Z" fill="url(#green-bottom)"/>
    </g>
    <use href="#teardrop" fill="none" stroke="var(--outline)" stroke-width="1"/>

    <!-- claim -->
    <text class="claim" x="614" y="195" font-size="12.5" textLength="91" lengthAdjust="spacingAndGlyphs">Safe &amp; Effective</text>
    <path class="claim-rule" d="M614,202 L705,202 L705,204 L614,204 Z M618,218 L703,206 L703,208 Z" fill="var(--white)"/>

    <!-- brand -->
    <g class="brand-lockup">
      <rect class="brand-square" x="500" y="350" width="66" height="66" rx="3" fill="var(--teal-accent)"/>
      <text class="brand-name" x="576" y="398" font-size="30" textLength="178" lengthAdjust="spacingAndGlyphs">Harbor Skin</text>
    </g>

    <!-- product name -->
    <g class="product-title" transform="rotate(-4 620 520)">
      <text class="product-line" x="618" y="496" font-size="30" text-anchor="middle" textLength="170" lengthAdjust="spacingAndGlyphs">Cutaneous</text>
      <text class="product-key" x="620" y="548" font-size="50" text-anchor="middle" textLength="184" lengthAdjust="spacingAndGlyphs">Comfort</text>
      <rect class="audience-pill" x="535" y="559" width="172" height="28" rx="8" fill="var(--orange)"/>
      <text class="audience" x="621" y="580" font-size="19" text-anchor="middle" textLength="150" lengthAdjust="spacingAndGlyphs">For Amputees</text>
      <text class="tagline" x="621" y="610" font-size="13" text-anchor="middle" textLength="172" lengthAdjust="spacingAndGlyphs">Experience Harbor find Calmness</text>
    </g>

    <!-- fine print -->
    <g class="fine-print" font-size="8">
      <text x="466" y="687">DIRECTIONS:</text>
      <text x="466" y="696">Spray on problem areas,</text>
      <text x="466" y="705">no need to dry off.</text>
      <text x="466" y="721">Harbor Skin Corpation</text>
      <text x="466" y="730">www.harborskin.example</text>
      <text x="466" y="740">MADE IN CANADA</text>
    </g>
    <text class="volume" x="690" y="725" font-size="19">500mL</text>
  </svg>
  <p class="panel-caption">Front</p>
</main>
</body>
</html>
```